High Tech Real Estate Startup needs a business card

We are developing an innovative real estate marketing product based around advanced search and virtual reality.

We talk to people, we need business cards.

Target Market(s)

The target market is technology professionals and realtors.

Contact Information for Business Card

The information to be included will include

Name
Title
Phone Number
E-mail Address
www.zelquin.com

It should use simple iconography for each one of those fields.

Font styles to use
Other font styles liked:
• Co, Jubilat, Avenir

Colors

Designer to choose colors to be used in the design.

Requirements
Must have
• Clean aesthetic,
• Good use of negative space.
• It should use our company logo, shown in the attached file. It is able to use the negative of that logo (coloured font and white background) and I have attached other acceptable accent colours in a swatch file.
Should not have
• Should not be too busy
• No extraneous text (slogans, tag lines etc)

```html
<!DOCTYPE html>
<html lang="en">
<head>
<meta charset="utf-8">
<title>Zelquin Business Card</title>
<link href="https://fonts.googleapis.com/css2?family=Nunito+Sans:wght@400;600&family=Open+Sans:wght@400;600&display=swap" rel="stylesheet">
<style>
  :root {
    --backdrop: #3a3a3c;
    --card: #1e1e20;
    --card-edge: #151516;
    --front-mark: #2c2c2f;
    --teal: #3fb7b9;
    --band-edge: #2a2a2c;
    --text-light: #f2f2f2;
    --text-muted: #5b5b5e;
  }
  html, body {
    margin: 0;
    padding: 0;
    width: 799px;
    height: 1200px;
    overflow: hidden;
    background: var(--backdrop);
  }
  .canvas {
    position: relative;
    width: 799px;
    height: 1200px;
  }
  .card {
    position: absolute;
    left: 110px;
    width: 580px;
    height: 330px;
    background: var(--card);
    border-radius: 26px;
    box-shadow: 0 14px 30px rgba(0,0,0,0.45), inset 0 0 0 1px var(--card-edge);
    overflow: hidden;
  }
  .card--front { top: 120px; }
  .card--back { top: 750px; }

  .front-name {
    position: absolute;
    inset: 0;
    display: flex;
    align-items: center;
    justify-content: center;
    font-family: "Nunito Sans", sans-serif;
    font-weight: 600;
    font-size: 72px;
    letter-spacing: 4px;
    color: var(--front-mark);
  }

  .accent-band {
    position: absolute;
    left: 0;
    top: 0;
    bottom: 0;
    width: 58px;
    background: var(--teal);
    border-right: 8px solid var(--band-edge);
  }
  .back-name {
    position: absolute;
    left: 96px;
    top: 34px;
    font-family: "Nunito Sans", sans-serif;
    font-weight: 600;
    font-size: 62px;
    letter-spacing: 3px;
    color: var(--teal);
    margin: 0;
  }
  .person {
    position: absolute;
    left: 96px;
    top: 156px;
    font-family: "Open Sans", sans-serif;
  }
  .person__name {
    margin: 0;
    font-weight: 600;
    font-size: 22px;
    color: var(--teal);
  }
  .person__title {
    margin: 2px 0 0;
    font-size: 13px;
    color: var(--text-muted);
  }
  .contacts {
    position: absolute;
    left: 96px;
    top: 232px;
    margin: 0;
    padding: 0;
    list-style: none;
    font-family: "Open Sans", sans-serif;
    font-size: 14px;
    color: var(--text-light);
  }
  .contacts li {
    display: flex;
    align-items: center;
    gap: 10px;
    height: 22px;
  }
  .contacts svg { width: 14px; height: 14px; flex: none; }
</style>
</head>
<body>
<main class="canvas">
  <section class="card card--front" aria-label="Card front">
    <div class="front-name">ZELQUIN</div>
  </section>

  <section class="card card--back" aria-label="Card back">
    <div class="accent-band"></div>
    <h1 class="back-name">ZELQUIN</h1>
    <div class="person">
      <p class="person__name">Dana Lee Parker</p>
      <p class="person__title">Managing Director</p>
    </div>
    <ul class="contacts">
      <li>
        <svg viewBox="0 0 14 14" aria-hidden="true"><circle cx="7" cy="7" r="7" fill="#3fb7b9"/><path d="M4.5 3.5h1.5l.7 1.8-.9.7a4 4 0 0 0 2.2 2.2l.7-.9 1.8.7v1.5c0 .4-.3.7-.7.7A5.8 5.8 0 0 1 3.8 4.2c0-.4.3-.7.7-.7z" fill="#1e1e20"/></svg>
        555.201.4837
      </li>
      <li>
        <svg viewBox="0 0 14 14" aria-hidden="true"><circle cx="7" cy="7" r="7" fill="#3fb7b9"/><rect x="3.5" y="4.5" width="7" height="5" fill="#1e1e20"/><path d="M3.5 4.5 7 7.3l3.5-2.8" stroke="#3fb7b9" stroke-width="0.8" fill="none"/></svg>
        dana@zelquin.com
      </li>
      <li>
        <svg viewBox="0 0 14 14" aria-hidden="true"><circle cx="7" cy="7" r="7" fill="#3fb7b9"/><circle cx="7" cy="7" r="3.6" fill="none" stroke="#1e1e20" stroke-width="0.9"/><path d="M3.4 7h7.2M7 3.4c-1.6 1.9-1.6 5.3 0 7.2M7 3.4c1.6 1.9 1.6 5.3 0 7.2" stroke="#1e1e20" stroke-width="0.8" fill="none"/></svg>
        www.zelquin.com
      </li>
    </ul>
  </section>
</main>
</body>
</html>
```